New business card for a regional office of a US M&A company

We need business card for a finance company, office based in Hong Kong , our Head office is in US, our business is to Merge and acquires companies , the new office will be a regional office for the Asia Pacific region. We want to use the head office logo as attached ( but don't have to be exactly the same, can be a variation to it) as a base and then add Asia Pacific alongside the logo.
We would prefer to have be bilingual Eng + Chinese, although we don't really have Chinese company name .

Industry/Entity Type

Business

Contact Information for Business Card

Clara Jo Tsang
 

VP,
APAC M&A Operations
ORIN VANTAGE Asia Pacific Limited
 
Unit 1407, K18
18 Tai Lok Shan Road, 
Hong Kong 
 
M: +852 6038 1742
T : +852 2836 4100
F : +852 2836 4177
VOIP: 4158
 
cjtsang@orinvantage.com

Font styles to use
Serif
Sans Serif

Colors

Designer to choose colors to be used in the design.

Requirements
Must have
• APAC Office

```html
<!DOCTYPE html>
<html lang="en">
<head>
<meta charset="utf-8">
<title>Orin Vantage — Business Card</title>
<link href="https://fonts.googleapis.com/css2?family=Open+Sans:wght@400;700&family=Oswald:wght@500&display=swap" rel="stylesheet">
<style>
  :root {
    --backdrop: #1a1a1a;
    --card: #262626;
    --card-edge: #2c2c2c;
    --accent: #1fb3cc;
    --ink: #f2f2f2;
  }
  * { box-sizing: border-box; margin: 0; padding: 0; }
  html, body {
    width: 1200px; height: 900px; overflow: hidden;
    background: radial-gradient(ellipse at 50% 40%, #2a2a2a 0%, var(--backdrop) 70%);
    font-family: "Open Sans", sans-serif;
    color: var(--ink);
  }
  .stage {
    width: 1200px; height: 900px;
    display: flex; flex-direction: column; align-items: center; justify-content: center;
    gap: 30px;
  }
  .card {
    position: relative;
    width: 700px; height: 400px;
    background: linear-gradient(135deg, var(--card) 0%, var(--card-edge) 100%);
    box-shadow: 0 12px 30px rgba(0,0,0,.55);
    overflow: hidden;
  }
  .card::after {
    content: ""; position: absolute; left: 0; right: 0; bottom: 0;
    height: 7px; background: var(--accent);
  }

  /* Front */
  .card-front { display: flex; flex-direction: column; align-items: center; justify-content: center; gap: 22px; }
  .brand-mark {
    width: 58px; height: 58px; border: 7px solid var(--ink);
  }
  .brand-name {
    font-weight: 700; font-size: 52px; letter-spacing: 2px;
    color: var(--accent); line-height: 1;
  }

  /* Back */
  .card-back .identity {
    position: absolute; right: 388px; top: 150px; text-align: right;
  }
  .person-name {
    font-family: "Oswald", sans-serif; font-weight: 500;
    font-size: 36px; color: var(--accent); text-transform: uppercase; line-height: 1.05;
  }
  .person-role { font-size: 17px; line-height: 1.3; margin-top: 6px; }
  .divider {
    position: absolute; left: 340px; top: 150px; width: 3px; height: 92px;
    background: var(--accent);
  }
  .contacts {
    position: absolute; left: 368px; top: 150px; list-style: none;
    font-size: 17px; line-height: 24px; letter-spacing: .5px;
  }
  .contacts li { display: flex; align-items: center; gap: 14px; }
  .contacts svg { width: 14px; height: 14px; fill: var(--accent); flex: none; }
  .footer {
    position: absolute; left: 40px; bottom: 34px;
    display: flex; align-items: center; gap: 12px; font-size: 19px;
  }
  .footer-brand { font-weight: 700; color: var(--accent); font-size: 19px; letter-spacing: .5px; }
  .footer-sep { width: 2px; height: 20px; background: var(--accent); }
</style>
</head>
<body>
<main class="stage">
  <section class="card card-front">
    <div class="brand-mark" aria-hidden="true"></div>
    <div class="brand-name">ORIN VANTAGE</div>
  </section>

  <section class="card card-back">
    <div class="identity">
      <div class="person-name">Clara Jo Tsang</div>
      <div class="person-role">VP,<br>APAC M&amp;A Operations</div>
    </div>
    <div class="divider"></div>
    <ul class="contacts">
      <li><svg viewBox="0 0 14 14"><path d="M4 0h6a1 1 0 0 1 1 1v12a1 1 0 0 1-1 1H4a1 1 0 0 1-1-1V1a1 1 0 0 1 1-1zm0 2v9h6V2z"/></svg>+852 6038 1742</li>
      <li><svg viewBox="0 0 14 14"><path d="M3 1l3 3-1.5 1.5a8 8 0 0 0 4 4L10 8l3 3-2 2C6 13 1 8 1 3z"/></svg>+852 2836 4100</li>
      <li><svg viewBox="0 0 14 14"><path d="M3 1h8v3H3zM1 5h12v6h-2V9H3v2H1zM4 10h6v3H4z"/></svg>+852 2836 4177</li>
      <li><svg viewBox="0 0 14 14"><path d="M0 3h14v1L7 8 0 4zM0 6l7 4 7-4v6H0z"/></svg>cjtsang@orinvantage.com</li>
    </ul>
    <div class="footer">
      <span class="footer-brand">ORIN VANTAGE</span>
      <span class="footer-sep"></span>
      <span>Unit 1407, K18 18 Tai Lok Shan Road, Hong Kong</span>
    </div>
  </section>
</main>
</body>
</html>
```